Vegan Alfredo Sauce Label Design for Bramble Kitchen Co

We are a food co. committed to making vegan food more accessible to people who want to eat healthier. Our first line of product is vegan Alfredo sauce.
We have 3 flavors:
- Garlic
- Pesto
- Lemony Artichoke
The current project is the design for the first flavor: garlic. However, we would like a template that would translate well to other flavors, so they look like a family of products.
These will be in standard 16 oz jars. The whole label will be approx 6cm x 24cm, but the front visual space is approx 6cm x 10cm. The rest will be nutritional labeling and copy about the company.
We also need a stamp or font- based logo that says Bramble Kitchen Co. (or lower case: bramble kitchen co.), the name of the company.
The picture (attached) of Vegan Queso is the closest to what we are going for. Because the sauce is creamy white, a colorful background with off-white font will be best.
We currently have a website, although we are doing a brand over-haul (hence, this posting) www.bramblekitchenco.example. If the designer is a good fit, we have several more projects, in line.
Other brands we love: Tidy Larder, Marlow Ridge Pantry, Pulp Poured Daily.
The final brand should communicate hip, natural and health.
And personally, I love design that is clever and somehow makes me smile.
Target Market(s)
Vegans, vegetarians, and people with common food allergies - all ages.
Young, hip families.
Industry/Entity Type
It Company
Requirements
Must have
- Copy:
Vegan Alfredo or Vegan Alfredo Sauce
Garlic
Bramble Kitchen or Bramble Kitchen Co
16 oz
Nice to have
- May include copy:
Gluten-Free Soy-Free Nut-Free
Should not have
- Neon colors

```html
<!DOCTYPE html>
<html lang="en">
<head>
<meta charset="utf-8">
<title>Bramble Kitchen Co — Vegan Alfredo Sauce Labels</title>
<link rel="stylesheet" href="https://fonts.googleapis.com/css2?family=Oswald:wght@500;600&family=Source+Sans+3:wght@400;600&display=swap">
<style>
  :root {
    --page: #ffffff;
    --cream: #eef0b9;
    --lemon: #c8b118;
    --garlic-bg: #a44a8d;
    --garlic-art: #7d2a6b;
    --garlic-band: #4a1d41;
    --artichoke-bg: #4f8a29;
    --artichoke-art: #3a6c20;
    --artichoke-band: #2d4a18;
    --pesto-bg: #7f9d23;
    --pesto-art: #62791b;
    --pesto-band: #485a16;
  }
  * { box-sizing: border-box; margin: 0; padding: 0; }
  html, body { width: 1200px; height: 903px; overflow: hidden; background: var(--page); }
  body { position: relative; font-family: "Source Sans 3", sans-serif; color: var(--cream); }

  .label {
    position: absolute; left: 124px; width: 954px; height: 238px;
    overflow: hidden; background: var(--bg);
  }
  .label--garlic { top: 71px; --bg: var(--garlic-bg); --art: var(--garlic-art); --band: var(--garlic-band); }
  .label--artichoke { top: 332px; --bg: var(--artichoke-bg); --art: var(--artichoke-art); --band: var(--artichoke-band); }
  .label--pesto { top: 594px; --bg: var(--pesto-bg); --art: var(--pesto-art); --band: var(--pesto-band); }

  .art {
    position: absolute; border-radius: 50%;
    background: radial-gradient(closest-side, var(--art) 55%, transparent 100%);
    opacity: .85;
  }

  .copy { position: absolute; inset: 0; text-align: center; }
  .copy > * { position: absolute; left: 0; right: 0; }

  .brand { font-size: 16px; font-weight: 400; letter-spacing: .2px; }
  .brand::before {
    content: ""; display: block; width: 6px; height: 6px; margin: 0 auto 2px;
    border-radius: 50%; background: var(--cream);
  }
  .kicker { font-family: "Oswald", sans-serif; font-weight: 500; font-size: 24px; letter-spacing: 1.5px; color: var(--lemon); }
  .flavor { font-family: "Oswald", sans-serif; font-weight: 600; line-height: 1; letter-spacing: 1px; }
  .product { line-height: 0; }
  .product span {
    display: inline-block; background: var(--band); padding: 0 8px;
    font-size: 17px; font-weight: 600; letter-spacing: 1.3px; line-height: 23px;
  }
  .claims { font-size: 11px; font-weight: 600; letter-spacing: 1.2px; }
  .size { font-size: 13px; }
</style>
</head>
<body>

<section class="label label--garlic">
  <div class="art" role="img" aria-label="Engraved garlic bulb illustration" style="left:-10px;top:40px;width:250px;height:240px"></div>
  <div class="art" role="img" aria-label="Engraved garlic bulb illustration" style="left:200px;top:-30px;width:180px;height:170px"></div>
  <div class="art" role="img" aria-label="Engraved garlic bulb illustration" style="left:560px;top:0;width:230px;height:240px"></div>
  <div class="art" role="img" aria-label="Engraved garlic bulb illustration" style="left:830px;top:80px;width:150px;height:180px"></div>
  <div class="copy">
    <p class="brand" style="top:14px">bramblekitchenco</p>
    <h2 class="flavor" style="top:55px;font-size:88px">GARLIC</h2>
    <p class="product" style="top:161px"><span>VEGAN ALFREDO SAUCE</span></p>
    <p class="claims" style="top:186px">GLUTEN-FREE • SOY-FREE • NUT-FREE</p>
    <p class="size" style="top:210px">16oz</p>
  </div>
</section>

<section class="label label--artichoke">
  <div class="art" role="img" aria-label="Artichoke illustration" style="left:0;top:50px;width:190px;height:210px"></div>
  <div class="art" role="img" aria-label="Artichoke illustration" style="left:215px;top:-10px;width:150px;height:140px"></div>
  <div class="art" role="img" aria-label="Artichoke illustration" style="left:560px;top:0;width:230px;height:240px"></div>
  <div class="art" role="img" aria-label="Artichoke illustration" style="left:830px;top:20px;width:150px;height:160px"></div>
  <div class="copy">
    <p class="brand" style="top:16px">bramblekitchenco</p>
    <p class="kicker" style="top:52px">LEMONY</p>
    <h2 class="flavor" style="top:86px;font-size:58px">ARTICHOKE</h2>
    <p class="product" style="top:163px"><span>VEGAN ALFREDO SAUCE</span></p>
    <p class="claims" style="top:186px">GLUTEN-FREE • SOY-FREE • NUT-FREE</p>
    <p class="size" style="top:210px">16oz</p>
  </div>
</section>

<section class="label label--pesto">
  <div class="art" role="img" aria-label="Basil leaves illustration" style="left:-10px;top:60px;width:240px;height:200px"></div>
  <div class="art" role="img" aria-label="Garlic bulb illustration" style="left:210px;top:-20px;width:200px;height:170px"></div>
  <div class="art" role="img" aria-label="Basil leaves illustration" style="left:560px;top:0;width:230px;height:240px"></div>
  <div class="art" role="img" aria-label="Garlic bulb illustration" style="left:790px;top:40px;width:180px;height:200px"></div>
  <div class="copy">
    <p class="brand" style="top:16px">bramblekitchenco</p>
    <h2 class="flavor" style="top:54px;font-size:90px">PESTO</h2>
    <p class="product" style="top:160px"><span>VEGAN ALFREDO SAUCE</span></p>
    <p class="claims" style="top:184px">GLUTEN-FREE • SOY-FREE • NUT-FREE</p>
    <p class="size" style="top:208px">16oz</p>
  </div>
</section>

</body>
</html>
```